Onboarding Carousel UI/UX design

We need a great UI/UX design for our onboarding carousel as attached in the PDF document. The chosen designers will be given our brand book with colors and styles to be used. The images must be focused on the content of each slide and be professional unique style (Do not use the childish cartoons we have used for placeholders)

Industry/Entity Type

Mortgage Brokerage

Number of Pages Required

5+ page

Font styles to use
Other font styles liked:
• Roboto

Requirements
Must have
• Great UI / UX design
Very relevant content of the images to match the slide
Nice to have
• Brand book

https://pv.lumorak.com/view/ed991dda-3474-4c3e-9747-882e21ba3df5-b8ca/?fullscreen

Image styles we like. Would need to be customized and made unique for us.

https://pinvarlo.com/shots/6300615-Torvane-Quillet-Illustration-Collaboration
https://meltridgestudio.co.za/software-client-style-frames
Should not have
• Do not use the childish images we have used as placeholders

```html
<!DOCTYPE html>
<html lang="en">
<head>
<meta charset="utf-8">
<title>Finance Brokerage – Onboarding Carousel</title>
<link href="https://fonts.googleapis.com/css2?family=Montserrat:wght@500&family=Roboto:wght@300;400;500;700&display=swap" rel="stylesheet">
<style>
  :root{
    --bg:#cfdef6;
    --screen:#ffffff;
    --hero:#dde6f8;
    --blue:#1f5bbf;
    --blue-text:#2a5bc7;
    --ink:#111318;
    --muted:#3a3d45;
    --dot:#c7ccd6;
    --art-a:#3d5be0;
    --art-b:#8fb0f2;
  }
  *{box-sizing:border-box;margin:0;padding:0}
  html,body{width:1200px;height:988px;overflow:hidden}
  body{background:var(--bg);font-family:'Roboto',sans-serif;color:var(--ink);position:relative}

  .project-title{position:absolute;left:0;top:188px;width:432px;text-align:center;font-family:'Montserrat',sans-serif;font-weight:500;font-size:60px;line-height:76px;color:#0b0b0d}

  .screen{position:absolute;width:176px;height:381px;background:var(--screen);border-radius:18px;overflow:hidden;box-shadow:0 14px 30px rgba(80,100,200,.25)}
  .status{position:absolute;top:8px;left:14px;right:12px;display:flex;justify-content:space-between;align-items:center;font-size:7px;z-index:2}
  .status svg{display:block}

  .hero{position:absolute;top:0;left:0;width:100%;height:135px}
  .hero-curve{position:absolute;inset:0}
  .art{position:absolute;left:50%;transform:translateX(-50%);top:22px;width:118px;height:96px;border-radius:14px;background:linear-gradient(140deg,var(--art-b),var(--art-a))}

  .content{position:absolute;left:0;right:0;top:136px;padding:0 5px;text-align:center}
  .step{font-size:12px;color:var(--blue-text);line-height:14px}
  .title{font-size:15px;font-weight:500;text-transform:uppercase;letter-spacing:.5px;line-height:20px;margin-top:2px;white-space:nowrap}
  .welcome .step{font-size:11.5px;text-transform:uppercase;letter-spacing:.3px}
  .rule{width:32px;height:2px;background:var(--blue);margin:3px auto 10px}
  .lead{font-size:9.4px;line-height:14.4px;color:var(--ink);white-space:nowrap}
  .note{font-size:7.2px;font-weight:300;line-height:14.4px;color:var(--muted);margin-top:12px;white-space:nowrap}

  .dots{position:absolute;top:317px;left:0;right:0;display:flex;justify-content:center;align-items:center;gap:4px}
  .dots.low{top:331px}
  .dots i{width:3.5px;height:3.5px;border-radius:50%;background:var(--dot)}
  .dots i.on{width:6px;height:6px;background:var(--blue);box-shadow:0 0 0 1.5px #b9cbef}

  .login{position:absolute;top:337px;left:0;right:0;text-align:center;font-size:5.5px;color:var(--muted)}
  .login a{color:var(--blue-text);text-decoration:none;margin-left:3px}
  .btn{position:absolute;top:351px;left:50%;transform:translateX(-50%);width:88px;height:17px;background:var(--blue);color:#fff;font-size:6.5px;font-weight:700;letter-spacing:.3px;display:flex;align-items:center;justify-content:center;border-radius:2px;box-shadow:0 3px 6px rgba(31,91,191,.3)}

  .perk-text{position:absolute;text-align:left}
  .perk-text h3{font-size:9.6px;font-weight:500;line-height:14.4px;white-space:nowrap}
  .perk-text .rule{margin:6px 0 7px;width:30px}
  .perk-text p{font-size:7.2px;font-weight:300;line-height:11.6px;color:var(--muted);white-space:nowrap}
  .perk-pic{position:absolute}
</style>
</head>
<body>

<h2 class="project-title">Finance<br>Brokerage</h2>

<!-- Welcome -->
<section class="screen welcome" style="left:434px;top:61px">
  <div class="status"><span>9:30</span><svg width="28" height="6" viewBox="0 0 28 6"><rect x="0" y="4" width="1.5" height="2" fill="#111"/><rect x="2.5" y="2.5" width="1.5" height="3.5" fill="#111"/><rect x="5" y="1" width="1.5" height="5" fill="#111"/><path d="M10 2.5a4 4 0 0 1 6 0M11.5 4a2 2 0 0 1 3 0" stroke="#111" fill="none" stroke-width=".9"/><rect x="19" y="1" width="8" height="4.2" rx="1" fill="#111"/></svg></div>
  <div class="hero"><svg class="hero-curve" viewBox="0 0 176 135" preserveAspectRatio="none"><path d="M0 0H176V110Q150 135 88 125Q30 118 0 70Z" fill="var(--hero)"/></svg><div class="art" role="img" aria-label="Illustration of a broker standing before a shield surrounded by insurance and loan icons" style="top:20px;height:92px"></div></div>
  <div class="content" style="top:129px">
    <div class="step">Welcome to</div>
    <h1 class="title" style="margin-top:0">Finance brokers<br>apply online</h1>
    <div class="rule" style="margin-top:3px"></div>
    <p class="lead">You can apply online for your<br>next mortgage credit in about<br>20 minutes.</p>
    <p class="note" style="margin-top:18px">It’s easy, and we will guide you all the way. See<br>the five simple steps that you have to take!</p>
  </div>
  <div class="dots"><i class="on"></i><i></i><i></i><i></i><i></i><i></i><i></i></div>
  <div class="login">Already have an account?<a href="#">Logon</a></div>
  <div class="btn">NEXT</div>
</section>

<!-- 01 -->
<section class="screen" style="left:700px;top:61px">
  <div class="status"><span>9:30</span><svg width="28" height="6" viewBox="0 0 28 6"><rect x="0" y="4" width="1.5" height="2" fill="#111"/><rect x="2.5" y="2.5" width="1.5" height="3.5" fill="#111"/><rect x="5" y="1" width="1.5" height="5" fill="#111"/><path d="M10 2.5a4 4 0 0 1 6 0M11.5 4a2 2 0 0 1 3 0" stroke="#111" fill="none" stroke-width=".9"/><rect x="19" y="1" width="8" height="4.2" rx="1" fill="#111"/></svg></div>
  <div class="hero"><svg class="hero-curve" viewBox="0 0 176 135" preserveAspectRatio="none"><path d="M0 0H176V110Q150 135 88 125Q30 118 0 70Z" fill="var(--hero)"/></svg><div class="art" role="img" aria-label="Illustration of people with a padlock and key beside a phone showing a sign-up form"></div></div>
  <div class="content">
    <div class="step">01</div>
    <h1 class="title">Create your<br>personal account</h1>
    <div class="rule"></div>
    <p class="lead">You will need a valid email<br>address to create your account</p>
    <p class="note" style="margin-top:13px">We will send you a confirmation email,<br>make sure you click the link to verify<br>your email address.</p>
  </div>
  <div class="dots"><i></i><i class="on"></i><i></i><i></i><i></i><i></i><i></i></div>
  <div class="btn">NEXT</div>
</section>

<!-- 02 -->
<section class="screen" style="left:965px;top:61px">
  <div class="status"><span>9:30</span><svg width="28" height="6" viewBox="0 0 28 6"><rect x="0" y="4" width="1.5" height="2" fill="#111"/><rect x="2.5" y="2.5" width="1.5" height="3.5" fill="#111"/><rect x="5" y="1" width="1.5" height="5" fill="#111"/><path d="M10 2.5a4 4 0 0 1 6 0M11.5 4a2 2 0 0 1 3 0" stroke="#111" fill="none" stroke-width=".9"/><rect x="19" y="1" width="8" height="4.2" rx="1" fill="#111"/></svg></div>
  <div class="hero"><svg class="hero-curve" viewBox="0 0 176 135" preserveAspectRatio="none"><path d="M0 0H176V110Q150 135 88 125Q30 118 0 70Z" fill="var(--hero)"/></svg><div class="art" role="img" aria-label="Illustration of a person seated beside a large phone showing a security code field and shield"></div></div>
  <div class="content">
    <div class="step">02</div>
    <h1 class="title">Secure your<br>account with your<br>mobile phone</h1>
    <div class="rule" style="margin:5px auto 6px"></div>
    <p class="lead">You will need a valid mobile<br>phone number to enable two factor<br>authentication.</p>
    <p class="note" style="margin-top:8px">We will send you an SMS containing<br>a security code to verify your mobile number.</p>
  </div>
  <div class="dots"><i></i><i></i><i class="on"></i><i></i><i></i><i></i><i></i></div>
  <div class="btn">NEXT</div>
</section>

<!-- 03 -->
<section class="screen" style="left:169px;top:528px">
  <div class="status"><span>9:30</span><svg width="28" height="6" viewBox="0 0 28 6"><rect x="0" y="4" width="1.5" height="2" fill="#111"/><rect x="2.5" y="2.5" width="1.5" height="3.5" fill="#111"/><rect x="5" y="1" width="1.5" height="5" fill="#111"/><path d="M10 2.5a4 4 0 0 1 6 0M11.5 4a2 2 0 0 1 3 0" stroke="#111" fill="none" stroke-width=".9"/><rect x="19" y="1" width="8" height="4.2" rx="1" fill="#111"/></svg></div>
  <div class="hero"><svg class="hero-curve" viewBox="0 0 176 135" preserveAspectRatio="none"><path d="M0 0H176V110Q150 135 88 125Q30 118 0 70Z" fill="var(--hero)"/></svg><div class="art" role="img" aria-label="Illustration of two people beside a large identity card" style="width:130px;height:76px;top:46px;background:linear-gradient(140deg,#6fe3d2,#3aa7b8)"></div></div>
  <div class="content">
    <div class="step">03</div>
    <h1 class="title">Verify your<br>identity online</h1>
    <div class="rule" style="margin:6px auto 5px"></div>
    <p class="lead">You will need to have a valid<br>Romanian ID card or residence permit</p>
    <p class="note" style="margin-top:9px">From your smart phone, you will<br>take a photo of your card and<br>make a selfie video.</p>
  </div>
  <div class="dots"><i></i><i></i><i></i><i class="on"></i><i></i><i></i><i></i></div>
  <div class="btn">NEXT</div>
</section>

<!-- 04 -->
<section class="screen" style="left:434px;top:528px">
  <div class="status"><span>9:30</span><svg width="28" height="6" viewBox="0 0 28 6"><rect x="0" y="4" width="1.5" height="2" fill="#111"/><rect x="2.5" y="2.5" width="1.5" height="3.5" fill="#111"/><rect x="5" y="1" width="1.5" height="5" fill="#111"/><path d="M10 2.5a4 4 0 0 1 6 0M11.5 4a2 2 0 0 1 3 0" stroke="#111" fill="none" stroke-width=".9"/><rect x="19" y="1" width="8" height="4.2" rx="1" fill="#111"/></svg></div>
  <div class="hero"><svg class="hero-curve" viewBox="0 0 176 135" preserveAspectRatio="none"><path d="M0 0H176V110Q150 135 88 125Q30 118 0 70Z" fill="var(--hero)"/></svg><div class="art" role="img" aria-label="Illustration of a laptop with a checklist form, a plant and a person" style="top:24px;height:104px"></div></div>
  <div class="content">
    <div class="step">04</div>
    <h1 class="title">Create your<br>profile data for<br>the application</h1>
    <div class="rule" style="margin:5px auto 5px"></div>
    <p class="lead">Tell us about your current situation<br>including employment, income,<br>assets and liabilities</p>
    <p class="note" style="margin-top:13px">It is essential to have everything as<br>accurate as possible so you can be<br>presented with the right offers.</p>
  </div>
  <div class="dots low"><i></i><i></i><i></i><i></i><i class="on"></i><i></i><i></i></div>
  <div class="btn">NEXT</div>
</section>

<!-- 05 -->
<section class="screen" style="left:700px;top:528px">
  <div class="status"><span>9:30</span><svg width="28" height="6" viewBox="0 0 28 6"><rect x="0" y="4" width="1.5" height="2" fill="#111"/><rect x="2.5" y="2.5" width="1.5" height="3.5" fill="#111"/><rect x="5" y="1" width="1.5" height="5" fill="#111"/><path d="M10 2.5a4 4 0 0 1 6 0M11.5 4a2 2 0 0 1 3 0" stroke="#111" fill="none" stroke-width=".9"/><rect x="19" y="1" width="8" height="4.2" rx="1" fill="#111"/></svg></div>
  <div class="hero"><svg class="hero-curve" viewBox="0 0 176 135" preserveAspectRatio="none"><path d="M0 0H176V110Q150 135 88 125Q30 118 0 70Z" fill="var(--hero)"/></svg><div class="art" role="img" aria-label="Illustration of a red house in front of a mortgage loan document with people and coins" style="width:160px;height:98px;background:linear-gradient(140deg,#9fb3ee,#ef6a5e)"></div></div>
  <div class="content">
    <div class="step">05</div>
    <h1 class="title">Apply for the<br>right loan for<br>your needs</h1>
    <div class="rule" style="margin:5px auto 6px"></div>
    <p class="lead">You will be presented with your<br>options, upload any supporting<br>documents and then submit your<br>application online.</p>
    <p class="note" style="margin-top:13px">Then we take it from here to get your approval.</p>
  </div>
  <div class="dots low"><i></i><i></i><i></i><i></i><i></i><i class="on"></i><i></i></div>
  <div class="btn">NEXT</div>
</section>

<!-- Benefits -->
<section class="screen" style="left:965px;top:528px">
  <div class="status"><span>9:30</span><svg width="28" height="6" viewBox="0 0 28 6"><rect x="0" y="4" width="1.5" height="2" fill="#111"/><rect x="2.5" y="2.5" width="1.5" height="3.5" fill="#111"/><rect x="5" y="1" width="1.5" height="5" fill="#111"/><path d="M10 2.5a4 4 0 0 1 6 0M11.5 4a2 2 0 0 1 3 0" stroke="#111" fill="none" stroke-width=".9"/><rect x="19" y="1" width="8" height="4.2" rx="1" fill="#111"/></svg></div>

  <div class="perk-pic" role="img" aria-label="Illustration of two businesspeople shaking hands beside coin stacks" style="left:84px;top:28px;width:92px;height:77px;background:linear-gradient(140deg,#e8eefc,#f3c56a)"></div>
  <div class="perk-text" style="left:13px;top:26px"><h3>Our service is<br>100% free</h3><div class="rule"></div><p>The banks pay us a<br>commission, so you<br>don’t have too.</p></div>

  <div class="perk-pic" role="img" aria-label="Illustration of a team working together around a table" style="left:2px;top:126px;width:84px;height:84px;border-radius:12px;background:linear-gradient(140deg,#8ee3d1,#e7b2ef)"></div>
  <div class="perk-text" style="left:99px;top:122px"><h3>Team of experts<br>here to help you</h3><div class="rule"></div><p>Our mortgage experts<br>stay by your side the<br>whole way, keeping<br>you in the loop.</p></div>

  <div class="perk-text" style="left:13px;top:223px"><h3>Made in Romania<br>with love</h3><div class="rule"></div><p>We love to help people<br>and would love to have<br>you as our customer</p></div>
  <div class="perk-pic" role="img" aria-label="Illustration of people assembling a large puzzle heart" style="left:90px;top:238px;width:84px;height:70px;border-radius:12px;background:linear-gradient(140deg,#f59ab5,#6f8fe6)"></div>

  <div class="dots low"><i></i><i></i><i></i><i></i><i></i><i></i><i class="on"></i></div>
  <div class="btn">GET STARTED</div>
</section>

</body>
</html>
```